Boutique custom software development company needs new business card

Our nearly 20 year old custom software development company would like to better include the fact that we are now providing Bitcoin services. These new services are B2B include education (how to acquire and securely hold Bitcoin) and integrating Bitcoin payments into existing ecommerce sites or other existing systems. Please keep the card clean and simple. Attached is our current design and some other files. vextorial.com

Target Market(s)

businesses owners interested in long term relationship

Industry/Entity Type

Custom software development and Bitcoin

Contact Information for Business Card

Dale Parker, dale@vextorial.com, vextorial.com, (888) 555-VXTRL

Font styles to use
Other font styles liked:
• monospace

Requirements
Must have
• double-sided
Nice to have
• clean and simple
Should not have
• physical address

```html
<!DOCTYPE html>
<html lang="en">
<head>
<meta charset="utf-8">
<title>Vextorial business card</title>
<link rel="stylesheet" href="https://fonts.googleapis.com/css2?family=Montserrat:wght@700;800&family=Lato:wght@400;700&display=swap">
<style>
  :root {
    --backdrop: #e4e4e2;
    --card: #2f2f30;
    --card-deep: #262627;
    --panel: #363637;
    --pattern: #3a3a3b;
    --orange: #f07a1e;
    --blue: #3d74c4;
    --white: #ffffff;
  }
  * { margin: 0; padding: 0; box-sizing: border-box; }
  html, body { width: 1200px; height: 801px; overflow: hidden; }
  body {
    background: var(--backdrop);
    font-family: "Lato", Arial, sans-serif;
    display: flex;
    align-items: center;
    justify-content: center;
    gap: 40px;
  }
  .card {
    position: relative;
    width: 520px;
    height: 297px;
    background: var(--card);
    border-bottom: 4px solid var(--orange);
    box-shadow: 0 10px 24px rgba(0,0,0,0.25);
    overflow: hidden;
  }

  /* front */
  .side-panel {
    position: absolute; top: 0; right: 0; bottom: 0; width: 230px;
    background: var(--panel);
  }
  .brand { position: absolute; left: 40px; top: 44px; }
  .brand-name {
    font-family: "Montserrat", Arial, sans-serif;
    font-weight: 800;
    font-size: 36px;
    letter-spacing: 0.5px;
    color: var(--blue);
    line-height: 1;
  }
  .brand-tagline { font-size: 14px; color: var(--blue); margin-top: 6px; }
  .person {
    position: absolute; left: 40px; top: 142px;
    font-family: "Montserrat", Arial, sans-serif;
    font-weight: 700; font-size: 20px; letter-spacing: 1px;
  }
  .person .first { color: var(--orange); }
  .person .last { color: var(--blue); }
  .contact { position: absolute; left: 40px; top: 188px; list-style: none; }
  .contact li {
    display: flex; align-items: center; gap: 10px;
    color: var(--white); font-size: 15px; line-height: 24px;
  }
  .contact svg { width: 14px; height: 14px; flex: none; }
  .services {
    position: absolute; right: 32px; top: 44px; list-style: none;
    color: var(--white); font-size: 14px; line-height: 20px; text-align: right;
  }
  .services .highlight { color: var(--orange); font-weight: 700; }

  /* back */
  .card-back { background: var(--card-deep); }
  .pattern-fill {
    position: absolute; inset: 0;
    background: linear-gradient(110deg, var(--card-deep) 0%, var(--pattern) 60%, #4a4a4b 100%);
  }
  .back-brand {
    position: absolute; left: 50%; top: 50%;
    transform: translate(-50%, -50%);
    display: flex; align-items: center; gap: 14px;
  }
  .back-mark { width: 58px; height: 58px; background: var(--blue); flex: none; }
  .back-brand .brand-name { color: var(--white); font-size: 36px; }
  .back-brand .brand-tagline { color: var(--white); font-size: 14px; }
</style>
</head>
<body>
  <section class="card card-front">
    <div class="side-panel"></div>
    <div class="brand">
      <div class="brand-name">VEXTORIAL</div>
      <div class="brand-tagline">developer of custom applications</div>
    </div>
    <div class="person"><span class="first">DALE</span> <span class="last">PARKER</span></div>
    <ul class="contact">
      <li>
        <svg viewBox="0 0 16 16"><path d="M4 1l3 3-2 2c1 2 3 4 5 5l2-2 3 3-2 2C7 14 2 9 2 3z" fill="var(--orange)"/></svg>
        (888) 555-VXTRL
      </li>
      <li>
        <svg viewBox="0 0 16 16"><rect x="1.5" y="3.5" width="13" height="9" fill="none" stroke="var(--orange)" stroke-width="1.5"/><path d="M1.5 3.5l6.5 5 6.5-5" fill="none" stroke="var(--orange)" stroke-width="1.5"/></svg>
        dale@vextorial.com
      </li>
      <li>
        <svg viewBox="0 0 16 16"><circle cx="8" cy="8" r="6.5" fill="none" stroke="var(--orange)" stroke-width="1.5"/><path d="M1.5 8h13M8 1.5c-3 3-3 10 0 13M8 1.5c3 3 3 10 0 13" fill="none" stroke="var(--orange)" stroke-width="1.2"/></svg>
        www.vextorial.com
      </li>
    </ul>
    <ul class="services">
      <li>custom software</li>
      <li class="highlight">bitcoin payments</li>
      <li class="highlight">bitcoin education</li>
    </ul>
  </section>

  <section class="card card-back">
    <div class="pattern-fill" role="img" aria-label="Embossed repeating brand pattern in dark grey"></div>
    <div class="back-brand">
      <div class="back-mark"></div>
      <div>
        <div class="brand-name">VEXTORIAL</div>
        <div class="brand-tagline">developer of custom applications</div>
      </div>
    </div>
  </section>
</body>
</html>
```